Business Card for Coastal Tundrabridge Advisory

We need a business card for Coastal Tundrabridge Advisory. The company website address is provided below. The company logo is attached. We provide specialized permafrost services to the mining, transportation, and oil & gas industries. The card should be prepared for:
Matthias Korhonen, PhD.
Coastal Tundrabridge Advisory
PO Box 418259
Quillwater, Alaska 99642
Direct: +1-907-555-0143
Email: mkorhonen@tundrabridgeadvisory.example
Website: www.coastaltundrabridgeadvisory.example

```html
<!DOCTYPE html>
<html lang="en">
<head>
<meta charset="utf-8">
<title>Coastal Tundrabridge Advisory — Business Card</title>
<link rel="stylesheet" href="https://fonts.googleapis.com/css2?family=Arimo:wght@400;700&display=swap">
<style>
  :root {
    --backdrop: #9a9a9a;
    --card-white: #fbfbfa;
    --card-dark: #0e151c;
    --ink: #1a232d;
    --ink-soft: #3a3f45;
    --ink-muted: #6b7076;
    --rule: #7d8287;
    --on-dark: #ffffff;
  }
  * { margin: 0; padding: 0; box-sizing: border-box; }
  html, body {
    width: 1200px; height: 1050px; overflow: hidden;
    background: var(--backdrop);
    font-family: "Arimo", Arial, sans-serif;
  }
  .canvas { position: relative; width: 1200px; height: 1050px; }

  .card { position: absolute; border-radius: 22px; }

  /* Front: portrait */
  .card-front {
    left: 90px; top: 190px; width: 380px; height: 665px;
    background: var(--card-white);
    color: var(--ink);
    display: flex; flex-direction: column; align-items: center;
    text-align: center;
    padding-top: 150px;
  }
  .front-wordmark {
    font-weight: 700; font-size: 21px; letter-spacing: 0.06em;
    line-height: 1.25; text-transform: uppercase; color: var(--ink);
  }
  .person-name {
    margin-top: 58px;
    font-weight: 700; font-size: 25px; color: var(--ink);
  }
  .person-title {
    margin-top: 6px;
    font-size: 17px; color: var(--ink-muted);
  }
  .icon-row {
    margin-top: 16px;
    display: flex; align-items: center; gap: 6px;
  }
  .icon-row .dash { width: 18px; height: 1px; background: var(--ink); }
  .icon-row svg { display: block; }
  .contact-list {
    margin-top: 22px;
    font-size: 15px; line-height: 1.45; color: var(--ink-soft);
  }
  .divider {
    margin-top: 28px; width: 70px; height: 1px; background: var(--rule);
  }
  .address {
    margin-top: 26px;
    font-size: 17px; line-height: 1.4; color: var(--ink-soft);
  }

  /* Back: landscape */
  .card-back {
    left: 540px; top: 360px; width: 580px; height: 331px;
    background: var(--card-dark);
    display: flex; align-items: center; justify-content: center;
  }
  .back-wordmark {
    color: var(--on-dark);
    font-weight: 700; font-size: 34px; letter-spacing: 0.08em;
    line-height: 1.3; text-transform: uppercase; text-align: center;
  }
</style>
</head>
<body>
<main class="canvas">

  <section class="card card-front" aria-label="Business card front">
    <div class="front-wordmark">Coastal Tundrabridge<br>Advisory</div>

    <h1 class="person-name">Matthias Korhonen, PhD.</h1>
    <p class="person-title">President</p>

    <div class="icon-row" aria-hidden="true">
      <span class="dash"></span>
      <svg width="20" height="20" viewBox="0 0 20 20">
        <circle cx="10" cy="10" r="10" fill="#1a232d"/>
        <path d="M7 5.5c.6-.4 1.2 0 1.5.6l.6 1.3c.2.5 0 .9-.4 1.2l-.5.4c.5 1 1.3 1.9 2.3 2.4l.4-.5c.3-.4.8-.5 1.2-.3l1.3.6c.6.3.9 1 .5 1.5-.6 1-1.7 1.3-2.8.8C8.7 12.4 7.4 11 6.5 8.6c-.4-1.2 0-2.4.5-3.1z" fill="#fff"/>
      </svg>
      <svg width="20" height="20" viewBox="0 0 20 20">
        <circle cx="10" cy="10" r="10" fill="#1a232d"/>
        <rect x="5" y="6.5" width="10" height="7" rx="0.8" fill="none" stroke="#fff" stroke-width="1.2"/>
        <path d="M5.3 7l4.7 3.6L14.7 7" fill="none" stroke="#fff" stroke-width="1.2"/>
      </svg>
      <svg width="20" height="20" viewBox="0 0 20 20">
        <circle cx="10" cy="10" r="10" fill="#1a232d"/>
        <circle cx="10" cy="10" r="5" fill="none" stroke="#fff" stroke-width="1.1"/>
        <ellipse cx="10" cy="10" rx="2.2" ry="5" fill="none" stroke="#fff" stroke-width="1"/>
        <path d="M5 10h10" stroke="#fff" stroke-width="1"/>
      </svg>
      <span class="dash"></span>
    </div>

    <div class="contact-list">
      <p class="contact-phone">+1-907-555-0143</p>
      <p class="contact-email">mkorhonen@tundrabridgeadvisory.example</p>
      <p class="contact-web">www.coastaltundrabridgeadvisory.example</p>
    </div>

    <span class="divider" aria-hidden="true"></span>

    <address class="address" style="font-style: normal;">
      PO Box 418259<br>
      Quillwater, Alaska 99642
    </address>
  </section>

  <section class="card card-back" aria-label="Business card back">
    <div class="back-wordmark">Coastal Tundrabridge<br>Advisory</div>
  </section>

</main>
</body>
</html>
```